Upgrade website from just a link tree to a full adult content site with payment gateway.

I would like to upgrade my website VelvetKestrel.com and turn it into a pay site with a payment gateway to my content. I would like to use Wordpress. The designer needs to produce a front page with membership sign up link, payment gateway which would then provide access to the content page. We would need to be able to then go in and edit (if necessary) and load all of the content. We would like this to be as easy as possible and already have paid for a Wordpress license. We could simply allow access to our hostnimbo/Wordpress account so you can build it once all the details are confirmed. Needs to be simple to upload and have a format all set to go where we would just log in and do it. May need directions or a tutorial to get us started on the path. We are open to suggestions and ideas. We will be providing adult content. Four pages I believe. Front page , gateway video content page and picture content page. The video and picture content goes really just need to be a layout and then we can drop the videos and images in there. You can ask any other relevant questions and we can update the brief. Sorry we are fairly new to this so this is why we are looking to professionals to lead the way. Please look at current webpage for an idea of how we like the current format. It can be replicated or it can be changed. We will market and funnel our online and SoCial accounts to this page on hopes people sign up and pay membership for access to the content past the first page. Check VelvetKestrel.com for an idea of how we want to move forward. Someone goes to page. We would like to see: They can click on member log in if they have already signed up or click join and go to the payment gateway page where they can choose their membership. Once they are paid they produce their log in and lassoed. Sign in and have access to the content pages. One page can be for photos and one page can be for videos. Would consider a live stream if possible but not mandatory. Basically we want to provide content people can view for a fee. A water mark would also be nice to protect our images and video. Also if there is a way to not allow the content to be downloaded. But a water mark would protect that.

Target Market(s)

Adult entertainment

Industry/Entity Type

Adult entertainment

Coding

Coded - Design and coding required

Number of Pages Required

4 page

Font styles to use
Decorative
Script

Colors
E54698
E96AAD
F1A4CE
F9D9EA
FCEFF6
A7469A
B969AE
D3A5CF
EDDBEB
F8F0F9

Requirements
Must have
• Front page. Gateway Payment/membership sign up. Video content page set up and image content page set up. Water mark we can put on content.
Nice to have
• Live video feed capabilities. Watermark.
Should not have
• Free access to the content.

```html
<!DOCTYPE html>
<html lang="en">
<head>
<meta charset="utf-8">
<title>VelvetKestrel — Home</title>
<link rel="stylesheet" href="https://fonts.googleapis.com/css2?family=Dancing+Script:wght@700&family=Montserrat:wght@400;500&display=swap">
<style>
  :root {
    --pink: #e9a6cc;
    --pink-strong: #e96aad;
    --white: #ffffff;
    --ink: #0a0909;
    --hero-ceiling: #c9c7c7;
    --hero-light: #8e8c8c;
    --hero-mid: #5c5a5a;
    --hero-dark: #262424;
    --rule: #3a3a3a;
  }
  * { margin: 0; padding: 0; box-sizing: border-box; }
  html, body { width: 1086px; height: 1200px; overflow: hidden; background: var(--ink); }
  body { position: relative; font-family: "Montserrat", Arial, sans-serif; color: var(--white); }
  a { color: inherit; text-decoration: none; }

  .hero {
    position: absolute; left: 0; top: 0; width: 1086px; height: 611px;
    background:
      radial-gradient(ellipse 420px 220px at 760px 110px, rgba(215,213,213,0.75), rgba(215,213,213,0) 100%),
      radial-gradient(ellipse 360px 160px at 460px 300px, rgba(70,68,68,0.6), rgba(70,68,68,0) 100%),
      radial-gradient(ellipse 520px 220px at 330px 520px, rgba(20,19,19,0.7), rgba(20,19,19,0) 100%),
      linear-gradient(170deg, var(--hero-light) 0%, var(--hero-mid) 50%, var(--hero-dark) 100%);
  }
  .brand {
    position: absolute; left: 62px; top: 40px;
    font-family: "Dancing Script", cursive; font-weight: 700; font-size: 42px; color: var(--white);
  }
  .contact-mail {
    position: absolute; right: 80px; top: 22px; font-size: 12px; display: flex; align-items: center; gap: 9px;
  }
  .main-nav { position: absolute; top: 52px; left: 0; width: 100%; height: 23px; font-size: 14px; }
  .main-nav a { position: absolute; top: 2px; color: var(--white); }
  .main-nav .current { text-decoration: underline; text-underline-offset: 3px; }
  .main-nav .login {
    top: 0; left: 955px; width: 51px; height: 23px; background: var(--pink); border-radius: 2px;
    font-size: 11px; line-height: 23px; text-align: center;
  }
  .hero-title {
    position: absolute; left: 0; width: 100%; top: 234px; text-align: center;
    font-family: "Dancing Script", cursive; font-weight: 700; font-size: 96px; line-height: 1;
  }
  .hero-title .accent { color: var(--pink); }
  .join-btn {
    position: absolute; left: 466px; top: 390px; width: 154px; height: 33px;
    border: 2px solid var(--white); border-radius: 9px; background: rgba(10,9,9,0.8);
    box-shadow: 0 0 6px var(--pink-strong);
    font-family: "Dancing Script", cursive; font-weight: 700; font-size: 20px; line-height: 29px; text-align: center; color: var(--white);
  }

  .about-title {
    position: absolute; left: 179px; top: 654px;
    font-family: "Dancing Script", cursive; font-weight: 700; font-size: 54px; color: var(--pink); line-height: 1.1;
  }
  .about-rule { position: absolute; left: 179px; top: 716px; width: 224px; height: 3px; background: var(--pink); }
  .about-text { position: absolute; left: 179px; top: 767px; width: 470px; font-size: 16.6px; line-height: 21px; }
  .about-text p + p { margin-top: 21px; }
  .portrait { position: absolute; left: 718px; top: 666px; }

  .social-row {
    position: absolute; left: 0; width: 100%; display: flex; justify-content: center; align-items: center;
    gap: 26px; font-size: 12px; line-height: 16px;
  }
  .social-row.first { top: 1046px; }
  .social-row.second { top: 1085px; gap: 30px; }
  .social-link { display: flex; align-items: center; gap: 22px; white-space: nowrap; }
  .mark { width: 14px; height: 14px; border-radius: 50%; background: var(--pink); flex: none; }
  .social-link svg { flex: none; }

  .footer-rule { position: absolute; left: 0; top: 1137px; width: 100%; height: 1px; background: var(--rule); }
  .copyright { position: absolute; left: 0; top: 1157px; width: 100%; text-align: center; font-size: 15px; }
  .copyright strong { font-weight: 500; }
</style>
</head>
<body>
  <header class="hero" role="img" aria-label="Black and white boudoir photograph of a woman reclining on a bed in a bedroom">
  </header>

  <div class="brand">VelvetKestrel</div>

  <div class="contact-mail">
    <svg width="16" height="11" viewBox="0 0 16 11" aria-hidden="true"><rect x="0.5" y="0.5" width="15" height="10" fill="none" stroke="#fff"/><path d="M0.5 0.5 L8 6.5 L15.5 0.5" fill="none" stroke="#fff"/></svg>
    <span>velvetkestrelxxx@inboxmail.com</span>
  </div>

  <nav class="main-nav">
    <a class="current" href="#" style="left:543px">Home</a>
    <a href="#" style="left:632px">Membership</a>
    <a href="#" style="left:768px">Videos</a>
    <a href="#" style="left:861px">Gallery</a>
    <a class="login" href="#">Login</a>
  </nav>

  <h1 class="hero-title">Queen Of <span class="accent">Dirty Talk</span></h1>
  <a class="join-btn" href="#">Join Now</a>

  <section class="about">
    <h2 class="about-title">About Me</h2>
    <div class="about-rule"></div>
    <div class="about-text">
      <p>I do things the other girls don’t! I suck and fuck like no other woman you’ll ever see. Filthy dirty talk, lots of sloppy oral, fantasy role play, dress up and cum swallowing.</p>
      <p>Cum watch me! Have your mind..... and your big fat load blown away!</p>
    </div>
    <svg class="portrait" width="254" height="334" viewBox="0 0 254 334">
      <defs>
        <linearGradient id="portraitTone" x1="0" y1="0" x2="1" y2="1">
          <stop offset="0" stop-color="#6a6868"/>
          <stop offset="0.5" stop-color="#d8d6d6"/>
          <stop offset="1" stop-color="#f2f2f2"/>
        </linearGradient>
      </defs>
      <circle cx="127" cy="147" r="120" fill="url(#portraitTone)" role="img" aria-label="Black and white portrait photograph"/>
      <circle cx="127" cy="147" r="120" fill="none" stroke="#e9a6cc" stroke-width="8"/>
    </svg>
  </section>

  <div class="social-row first">
    <a class="social-link" href="#"><span class="mark"></span><span>www.fanvault.com/velvetkestrel</span></a>
    <a class="social-link" href="#">
      <svg width="14" height="17" viewBox="0 0 14 17" aria-hidden="true"><path d="M3.5 7 V4.5 a3.5 3.5 0 0 1 7 0 V7" fill="none" stroke="#e9a6cc" stroke-width="1.3"/><rect x="1" y="7" width="12" height="9" rx="2" fill="none" stroke="#e9a6cc" stroke-width="1.3"/><circle cx="7" cy="11.3" r="1.2" fill="#e9a6cc"/></svg>
      <span>www.fanvault.com/velvetkestrelvip</span>
    </a>
    <a class="social-link" href="#"><span class="mark"></span><span>https://paywisp.com/code?user_id=5830192746518203917</span></a>
  </div>
  <div class="social-row second">
    <a class="social-link" href="#"><span class="mark"></span><span>https://vidstream.com/channel/VK7rTqPzLmWnb4XoYeHsD_a</span></a>
    <a class="social-link" href="#"><span class="mark"></span><span>https://snapgram.com/velvetkestrel9?r=nametag</span></a>
  </div>

  <div class="footer-rule"></div>
  <footer class="copyright">Copyright © 2020-2021 VelvetKestrel | <strong>Privacy</strong> | <strong>Terms</strong></footer>
</body>
</html>
```